Lawn Sign Design – Brisqel

We need a clean, eye-catching 18" x 24" lawn sign for Brisqel that effectively communicates our core message while maintaining strong brand consistency.

Key Elements to Include:
Tagline (Main Focus): Upgrade Your Roof Without Replacing It
Website: www.trybrisqel.com
Phone Number: (888) BRISQEL-GO
TWQB License Number: 4480512
Brisqel Logo & Branding: Ensure the logo, corporate colors, and custom font are used consistently to align with our existing branding.

Design Guidelines:
Simple & High-Impact: The tagline should be the most prominent element on the sign, drawing immediate attention.
Easy Readability: Use a bold, clean design with high contrast for quick readability from a distance.
Balanced Layout: Place supporting details (website, phone number, and TWQB number) in a visually clear but secondary position to the tagline.
Professional & Modern: The sign should reflect credibility and innovation in the roofing industry.

Deliverables:
High-resolution print-ready files (CMYK)
A digital proof for review before finalizing
The final design should make a strong impression with minimal text, ensuring that anyone passing by can instantly grasp what we offer.

I am including our custom font. To get an hexagon in our name, simply type the $ after the 'O" Please use this font for anything you type.

```html
<!DOCTYPE html>
<html lang="en">
<head>
<meta charset="utf-8">
<title>Brisqel Lawn Sign</title>
<link rel="stylesheet" href="https://fonts.googleapis.com/css2?family=Archivo+Black&family=Poppins:wght@500;600;700&family=Yellowtail&display=swap">
<style>
  :root {
    --backdrop: #d9d9d9;
    --paper: #ffffff;
    --brand-blue: #17519a;
    --brand-navy: #0f2f63;
    --ink: #1a1a1a;
    --frame-line: #7a7a7a;
  }
  html, body {
    margin: 0;
    width: 1200px;
    height: 1200px;
    overflow: hidden;
    background: var(--backdrop);
  }
  .lawn-sign {
    position: absolute;
    left: 150px;
    top: 0;
    width: 900px;
    height: 1200px;
    display: block;
  }
  .sign-paper { fill: var(--paper); }
  .sign-band { fill: var(--brand-blue); }
  .sign-frame { fill: none; stroke: var(--frame-line); stroke-width: 2.5; }
  .brand-name {
    font-family: 'Poppins', sans-serif;
    font-weight: 700;
    fill: var(--brand-blue);
  }
  .headline-dark {
    font-family: 'Archivo Black', sans-serif;
    fill: var(--ink);
  }
  .headline-roof {
    font-family: 'Archivo Black', sans-serif;
    fill: var(--brand-blue);
  }
  .headline-script {
    font-family: 'Yellowtail', cursive;
    fill: var(--ink);
  }
  .contact-phone {
    font-family: 'Poppins', sans-serif;
    font-weight: 700;
    fill: var(--paper);
  }
  .contact-web {
    font-family: 'Poppins', sans-serif;
    font-weight: 600;
    fill: var(--paper);
  }
  .license-pill { fill: var(--brand-navy); }
  .license-text {
    font-family: 'Poppins', sans-serif;
    font-weight: 500;
    fill: var(--paper);
  }
  .phone-badge { fill: var(--paper); }
  .phone-badge-ring { fill: none; stroke: var(--brand-blue); stroke-width: 3; }
  .phone-icon { fill: var(--ink); }
  .phone-waves { fill: none; stroke: var(--ink); stroke-width: 1.6; stroke-linecap: round; }
</style>
</head>
<body>
<svg class="lawn-sign" viewBox="0 0 900 1200" xmlns="http://www.w3.org/2000/svg">
  <rect class="sign-paper" x="0" y="0" width="900" height="1200"/>
  <polygon class="sign-band" points="0,698 450,842 900,698 900,1200 0,1200"/>
  <rect class="sign-frame" x="50" y="50" width="800" height="1101"/>

  <text class="brand-name" x="450" y="272" font-size="112" text-anchor="middle" textLength="500" lengthAdjust="spacingAndGlyphs">BRISQEL</text>

  <text class="headline-dark" x="450" y="427" font-size="74" text-anchor="middle" textLength="596" lengthAdjust="spacingAndGlyphs">UPGRADE YOUR</text>
  <text class="headline-roof" x="450" y="567" font-size="176" text-anchor="middle" textLength="493" lengthAdjust="spacingAndGlyphs">ROOF</text>
  <text class="headline-script" x="450" y="628" font-size="78" text-anchor="middle" textLength="259" lengthAdjust="spacingAndGlyphs">Without</text>
  <text class="headline-dark" x="450" y="712" font-size="72" text-anchor="middle" textLength="518" lengthAdjust="spacingAndGlyphs">REPLACING IT</text>

  <g class="phone-mark" transform="translate(450 842)">
    <circle class="phone-badge" r="54"/>
    <circle class="phone-badge-ring" r="45"/>
    <path class="phone-icon" d="M-22,-22 c3,-3 8,-3 10,0 l7,9 c2,3 1,6 -1,8 l-4,4 c3,7 9,13 16,16 l4,-4 c2,-2 5,-3 8,-1 l9,7 c3,2 3,7 0,10 l-5,5 c-4,4 -12,4 -20,-1 c-12,-7 -22,-17 -29,-29 c-5,-8 -5,-16 -1,-20 z"/>
    <path class="phone-waves" d="M4,-16 a12,12 0 0 1 12,12 M4,-23 a19,19 0 0 1 19,19 M4,-30 a26,26 0 0 1 26,26"/>
  </g>

  <text class="contact-phone" x="450" y="983" font-size="70" text-anchor="middle" textLength="570" lengthAdjust="spacingAndGlyphs">(888) BRISQEL-GO</text>
  <text class="contact-web" x="450" y="1044" font-size="60" text-anchor="middle" textLength="640" lengthAdjust="spacing" letter-spacing="4">www.trybrisqel.com</text>

  <rect class="license-pill" x="245" y="1075" width="413" height="40" rx="6"/>
  <text class="license-text" x="451" y="1103" font-size="22" text-anchor="middle">TWQB License Number: 4480512</text>
</svg>
</body>
</html>
```